Motivational Poster Design Project

I would like to create a poster with some of my favorite quotes to hang in my office. I did a similar project in 2012 and I've uploaded the top 2 designs so you can get a better idea of what I'm looking for. I will provide feedback on your design within 24 hours of receiving it.

The poster must contain the following quotes:

"You’re only given a little spark of madness. You mustn’t lose it.”
- Dorian Fletcher

“The most contrarian thing of all is not to oppose the crowd but to think for yourself.”
- Marcus Olden

"I constantly see people rise in life who are not the smartest, sometimes not even the most diligent, but they are learning machines. They go to bed every night a little wiser than they were when they got up and boy does that help, particularly when you have a long run ahead of you."
- Frankie Dalgarth

“In theory, there’s no difference between theory and practice. But, in practice, there is.”
- Kees R. T. Ter Haverkamp

"At the end of the day, a reactionary life is a normal life. One thing is consistent in every remarkable person: they decide to do something remarkable. Don’t let the world choose who you become."
- Rohan Kapadia

“It usually takes 3-4 months to try enough that you can do a proper 80/20 analysis, then two months to design systems to scale what *is* working.”
-Ned Yarrow

“Authority is 20 percent given, 80 percent taken.”
- Glenn Mosbacker

“Your actions are consistent with the way the world occurs to you.”
- Dieter Kolbach

Project Deadline Extended
Reason: I am going to be travelling with no access to internet until January 5th, 2015. I am extending the project deadline until 12/31/14 and I'll make a final decision during the 1st week of January.

Target Market(s)

Personal Project

Industry/Entity Type

Learning

Requirements
Must have
• The poster will be 24" high x 36" long and printed on canvas, so the image you create needs to have a resolution of at least 2700 x 3900.
Nice to have
• I don't have an exact vision for how the poster should look, so I am totally open to you using your creativity to develop, arrange and present the content as you'd like.
• That said, I would like an image (photo or posterized image) of the person being quoted along with each quote. I do not have specific images that I would like you to use, so you will need to find the images on your own. The images don't need to be perfect... I am more interested in the poster relating the essence of the quotes and the people being quoted than I am in perfect photographic images of the people being quoted.

```html
<!DOCTYPE html>
<html lang="en">
<head>
<meta charset="utf-8">
<title>Quote Poster</title>
<link rel="stylesheet" href="https://fonts.googleapis.com/css2?family=Roboto+Condensed:wght@400;700&display=swap">
<style>
  :root {
    --bg-light: #f4f6f8;
    --bg-mid: #d9dee4;
    --bg-edge: #b9c0c8;
    --green: #3f9a3a;
    --green-dark: #2c7a2a;
    --blue: #24579a;
    --blue-dark: #173f78;
    --purple: #9b3f9a;
    --purple-dark: #76277a;
    --teal: #1f9aa8;
    --teal-dark: #137683;
    --tan: #a48d74;
    --tan-dark: #86705a;
    --red: #c42a45;
    --red-dark: #9c1c33;
    --forest: #2c8a5e;
    --forest-dark: #1d6b47;
    --orange: #d8782a;
    --orange-dark: #b45c18;
    --ink: #ffffff;
    --frame: #ffffff;
    --photo-empty: #c8c8c8;
  }
  * { box-sizing: border-box; margin: 0; padding: 0; }
  html, body { width: 800px; height: 1200px; overflow: hidden; }
  body { background: var(--bg-light); font-family: "Roboto Condensed", "Arial Narrow", sans-serif; }
  .poster {
    position: relative; width: 800px; height: 1200px; overflow: hidden;
    background: radial-gradient(ellipse at 50% 45%, var(--bg-light) 0%, var(--bg-mid) 75%, var(--bg-edge) 100%);
    border: 12px solid #fff;
    box-shadow: inset 0 0 0 1px #c5cbd2;
  }
  .band {
    position: absolute;
    transform: rotate(-1.6deg);
    box-shadow: 0 4px 8px rgba(0,0,0,.3);
  }
  .quote {
    position: absolute;
    color: var(--ink);
    font-weight: 700;
    font-size: 20px;
    line-height: 1.26;
    transform: rotate(-1.6deg);
    text-shadow: 0 1px 1px rgba(0,0,0,.25);
  }
  .quote cite {
    display: block; text-align: right; font-style: normal; font-weight: 400; margin-top: 2px;
  }
  .portrait {
    position: absolute;
    border: 6px solid var(--frame);
    box-shadow: 0 4px 10px rgba(0,0,0,.35);
  }
  .band--green  { left: 10px;  top: 34px;   width: 520px; height: 105px; background: linear-gradient(90deg, var(--green-dark), var(--green)); }
  .band--blue   { left: 170px; top: 152px;  width: 620px; height: 132px; background: linear-gradient(90deg, var(--blue), var(--blue-dark)); }
  .band--purple { left: 10px;  top: 290px;  width: 770px; height: 198px; background: linear-gradient(90deg, var(--purple-dark), var(--purple)); }
  .band--teal   { left: 135px; top: 510px;  width: 630px; height: 100px; background: linear-gradient(90deg, var(--teal), var(--teal-dark)); }
  .band--tan    { left: 10px;  top: 632px;  width: 700px; height: 175px; background: linear-gradient(90deg, var(--tan-dark), var(--tan)); }
  .band--red    { left: 40px;  top: 808px;  width: 750px; height: 145px; background: linear-gradient(90deg, var(--red), var(--red-dark)); }
  .band--forest { left: 10px;  top: 940px;  width: 492px; height: 122px; background: linear-gradient(90deg, var(--forest-dark), var(--forest)); }
  .band--orange { left: 250px; top: 1055px; width: 540px; height: 108px; background: linear-gradient(90deg, var(--orange), var(--orange-dark)); }

  .quote--green  { left: 215px; top: 52px;  width: 300px; font-size: 21px; }
  .quote--blue   { left: 190px; top: 180px; width: 400px; }
  .quote--purple { left: 217px; top: 298px; width: 540px; }
  .quote--teal   { left: 153px; top: 520px; width: 440px; }
  .quote--tan    { left: 218px; top: 650px; width: 470px; }
  .quote--red    { left: 128px; top: 812px; width: 465px; }
  .quote--forest { left: 210px; top: 960px; width: 280px; }
  .quote--orange { left: 272px; top: 1070px; width: 320px; }

  .portrait--1 { left: 42px;  top: 30px;   width: 158px; height: 158px; background: linear-gradient(160deg, #e8e8e8, #8a8a8a 70%, #2a2a2a); }
  .portrait--2 { left: 606px; top: 88px;   width: 156px; height: 155px; background: linear-gradient(160deg, #f2f2f2, #9a9a9a 60%, #3b3f47); }
  .portrait--3 { left: 43px;  top: 323px;  width: 152px; height: 147px; background: linear-gradient(160deg, #4a6fa8, #c8a48a 55%, #2c3444); }
  .portrait--4 { left: 608px; top: 488px;  width: 150px; height: 150px; background: var(--photo-empty); }
  .portrait--5 { left: 43px;  top: 637px;  width: 152px; height: 146px; background: linear-gradient(160deg, #d8d8d8, #a07a62 55%, #3a3e44); }
  .portrait--6 { left: 608px; top: 820px;  width: 155px; height: 150px; background: linear-gradient(160deg, #ffffff, #d7a88c 55%, #c8323a); }
  .portrait--7 { left: 40px;  top: 933px;  width: 150px; height: 147px; background: linear-gradient(160deg, #3b6fc0, #c89880 55%, #2a2e3a); }
  .portrait--8 { left: 608px; top: 1010px; width: 150px; height: 150px; background: linear-gradient(160deg, #d0d0d0, #a88a78 55%, #2a2a2a); }
</style>
</head>
<body>
<main class="poster">
  <div class="band band--green"></div>
  <div class="band band--blue"></div>
  <div class="band band--purple"></div>
  <div class="band band--teal"></div>
  <div class="band band--tan"></div>
  <div class="band band--red"></div>
  <div class="band band--forest"></div>
  <div class="band band--orange"></div>

  <div class="portrait portrait--1" role="img" aria-label="Portrait photo of Dorian Fletcher"></div>
  <div class="portrait portrait--2" role="img" aria-label="Portrait photo of Marcus Olden"></div>
  <div class="portrait portrait--3" role="img" aria-label="Portrait photo of Frankie Dalgarth"></div>
  <div class="portrait portrait--4" role="img" aria-label="Portrait placeholder for Kees R. T. Ter Haverkamp"></div>
  <div class="portrait portrait--5" role="img" aria-label="Portrait photo of Rohan Kapadia"></div>
  <div class="portrait portrait--6" role="img" aria-label="Portrait photo of Ned Yarrow"></div>
  <div class="portrait portrait--7" role="img" aria-label="Portrait photo of Glenn Mosbacker"></div>
  <div class="portrait portrait--8" role="img" aria-label="Portrait photo of Dieter Kolbach"></div>

  <blockquote class="quote quote--green">You’re only given a little spark of madness. You mustn’t lose it.<cite>- Dorian Fletcher</cite></blockquote>
  <blockquote class="quote quote--blue">The most contrarian thing of all is not to oppose the crowd but to think for yourself.<cite>- Marcus Olden</cite></blockquote>
  <blockquote class="quote quote--purple">I constantly see people rise in life who are not the smartest, sometimes not even the most diligent, but they are learning machines. They go to bed every night a little wiser than they were when they got up and boy does that help, particularly when you have a long run ahead of you..<cite>- Frankie Dalgarth</cite></blockquote>
  <blockquote class="quote quote--teal">In theory, there's no difference between theory and practice. But, in practice, there is.<cite>- Kees R. T. Ter Haverkamp</cite></blockquote>
  <blockquote class="quote quote--tan">At the end of the day, a reactionary life is a normal life. One thing is consistent in every remarkable person: they decide to do something remarkable. Don’t let the world choose who you become.<cite>- Rohan Kapadia</cite></blockquote>
  <blockquote class="quote quote--red">It usually takes 3-4 months to try enough that you can do a proper 80/20 analysis, then two months to design systems to scale what *is* working.<cite>-Ned Yarrow</cite></blockquote>
  <blockquote class="quote quote--forest">Authority is 20 percent given, 80 percent taken.<cite>- Glenn Mosbacker</cite></blockquote>
  <blockquote class="quote quote--orange">Your actions are consistent with the way the world occurs to you.<cite style="text-align:left">- Dieter Kolbach</cite></blockquote>
</main>
</body>
</html>
```